Stationary - Based On Previous Design

Basic stationary with a header and footer

Target Market(s)

Friends, Colleagues, More friendly than professional

Industry/Entity Type

legal/personal

Colors
00AB8E
00BBA5
67D7C9
C6EFE9
E9F9F6

Requirements
Must have
• Green & White
Nice to have
• I like the "G" on the business card and was thinking that would be for both G's in "PellaNote"
Should not have
• other colors

```html
<!DOCTYPE html>
<html lang="en">
<head>
<meta charset="utf-8">
<title>PellaNote Envelopes</title>
<link href="https://fonts.googleapis.com/css2?family=Oswald:wght@600&family=Roboto:wght@400&display=swap" rel="stylesheet">
<style>
  :root {
    --backdrop: #E9F9F6;
    --paper: #ffffff;
    --ink: #1f2a28;
    --ink-soft: #3b4644;
    --brand-teal: #00AB8E;
    --brand-teal-bright: #00BBA5;
    --teal-mid: #67D7C9;
    --watermark: #C6EFE9;
  }
  * { box-sizing: border-box; margin: 0; padding: 0; }
  html, body {
    width: 1200px;
    height: 795px;
    overflow: hidden;
    background: var(--backdrop);
  }
  .stationery {
    position: relative;
    width: 1200px;
    height: 795px;
  }
  .envelope {
    position: absolute;
    width: 540px;
    height: 246px;
    background: var(--paper);
    overflow: hidden;
    box-shadow: 0 2px 8px rgba(0, 171, 142, 0.15);
  }
  .envelope--front { left: 40px; top: 275px; }
  .envelope--back  { left: 620px; top: 275px; }

  .return-address {
    position: absolute;
    left: 26px;
    top: 22px;
    display: flex;
    align-items: flex-end;
    gap: 10px;
  }
  .return-address__text {
    display: flex;
    flex-direction: column;
    gap: 2px;
  }
  .wordmark {
    font-family: "Oswald", sans-serif;
    font-weight: 600;
    font-size: 24px;
    letter-spacing: 0.3px;
    line-height: 1.2;
    color: var(--ink);
    margin-bottom: 2px;
  }
  .address {
    font-family: "Roboto", sans-serif;
    font-size: 12px;
    line-height: 1.35;
    color: var(--ink-soft);
  }
  .brand-dot {
    width: 34px;
    height: 34px;
    border-radius: 50%;
    background: var(--brand-teal);
    margin-bottom: 20px;
  }
  .watermark-circle {
    position: absolute;
    right: -30px;
    bottom: -70px;
    width: 250px;
    height: 250px;
    border-radius: 50%;
    background: var(--watermark);
  }

  .flap { position: absolute; inset: 0; }
  .flap-mark {
    position: absolute;
    left: 0;
    right: 0;
    top: 44px;
    text-align: center;
    font-family: "Oswald", sans-serif;
    font-weight: 600;
    font-size: 16px;
    letter-spacing: 1px;
    line-height: 1.2;
    color: var(--paper);
  }
</style>
</head>
<body>
  <main class="stationery">
    <section class="envelope envelope--front" aria-label="Envelope front">
      <div class="watermark-circle" aria-hidden="true"></div>
      <div class="return-address">
        <div class="return-address__text">
          <span class="wordmark">PELLA NOTE</span>
          <span class="address">418 N Larkin Ave</span>
          <span class="address">Dayton, OH 45402</span>
        </div>
        <div class="brand-dot" aria-hidden="true"></div>
      </div>
    </section>

    <section class="envelope envelope--back" aria-label="Envelope back">
      <svg class="flap" width="540" height="246" viewBox="0 0 540 246" aria-hidden="true">
        <path d="M0 0 H540 V120 Q540 128 530 128 L90 128 Q40 128 14 100 Q0 88 0 70 Z" fill="var(--brand-teal)"/>
      </svg>
      <div class="flap-mark">PELLANOTE</div>
    </section>
  </main>
</body>
</html>
```